Boutique Real Estate Brokerage Tessly Realty Website Design

Winning designer work on migrate as well through nest ferry.
We need a new website as an informational hub to aid our print and digital strategy as well as showing that we are located in Brooklyn and Florida. I have a boutique real estate brokerage and advisory firm specializing in residential leasing, multifamily sales and 1031 Exchange appropriation. This won't be a portal to search properties, it will be a place for information. I'd like space for an ebook to be downloaded and information on my probate sales and multifamily leasing marketing campaigns. I included my logo and will leave it up to the designer to come up with colors to match it. I have also attached verbiage for each page. The final design should have a modern high end look that reflects gentrifying Brooklyn as well as beautiful Florida.
Thank you!
Target Market(s)
Owners of income producing real estate and develop-able land in Brooklyn, NY and Florida.
Industry/Entity Type
Real Estate
Coding
Coded - Design and coding required
Number of Pages Required
5+ page
Colors
Designer to choose colors to be used in the design.
Requirements
Must have
- A modern elegant look
Nice to have
- pictures of brooklyn and florida
Should not have
- real estate search pages

```html
<!DOCTYPE html>
<html lang="en">
<head>
<meta charset="utf-8">
<title>Tessly Realty</title>
<link href="https://fonts.googleapis.com/css2?family=Orbitron:wght@700;800&family=Raleway:wght@400;500;600;700&display=swap" rel="stylesheet">
<style>
:root{
  --black:#0b0b0b;
  --dark:#252525;
  --white:#ffffff;
  --text:#333333;
  --muted:#cfcfcf;
  --line:#e2e2e2;
  --brick:#6b3b2a;
  --leaf:#3d5a2a;
  --sky:#9fb3c4;
  --sea:#2c4a5c;
}
*{box-sizing:border-box;margin:0;padding:0}
html,body{width:1200px;height:4009px;overflow:hidden}
body{position:relative;font-family:"Raleway",sans-serif;color:var(--text);background:var(--white)}
.abs{position:absolute}
.display{font-family:"Orbitron",sans-serif;font-weight:800;letter-spacing:2px}

/* header */
.site-header{left:0;top:0;width:1200px;height:107px;background:var(--black)}
.brand{left:88px;top:26px;display:flex;align-items:center;gap:14px;color:var(--white);font-weight:700;font-size:17px;letter-spacing:3px;text-transform:uppercase}
.brand-mark{width:54px;height:54px;border-radius:50%;background:#8a8a8a}
.main-nav{left:545px;top:40px;display:flex;gap:45px;color:var(--white);font-size:17px}
.main-nav svg{margin-left:22px;vertical-align:middle}
.top-bar{left:0;top:107px;width:1200px;height:51px;background:var(--white);font-size:16px;color:#222}
.top-bar .left{left:90px;top:15px;display:flex;gap:40px}
.top-bar .right{right:88px;top:15px;display:flex;gap:35px}
.top-bar svg{vertical-align:-2px;margin-right:8px}

/* hero */
.hero{left:0;top:158px;width:1200px;height:628px;background:linear-gradient(90deg,#3a3a30 0%,var(--brick) 35%,#7a4530 60%,var(--leaf) 100%)}
.hero-title{left:0;top:252px;width:1200px;text-align:center;color:var(--white);font-size:35px;line-height:46px;text-transform:uppercase}
.hero-dots{left:540px;top:705px;display:flex;gap:12px}
.hero-dots span{width:16px;height:16px;border:2px solid var(--white)}
.hero-dots span:first-child{background:var(--white)}

/* intro band */
.intro{left:0;top:786px;width:1200px;height:272px;background:var(--dark);color:var(--white)}
.intro h2{left:90px;top:98px;font-weight:500;font-size:28px}
.intro p{left:90px;top:138px;font-size:18px;color:var(--muted)}
.btn{display:inline-flex;align-items:center;justify-content:center;font-size:18px}
.btn-outline{left:800px;top:106px;width:146px;height:55px;border:2px solid var(--white);color:var(--white)}
.btn-light{left:962px;top:106px;width:146px;height:55px;background:var(--white);color:#111}

/* services */
.section-title{left:0;top:1188px;width:1200px;text-align:center;font-size:34px;color:#111}
.service-img{width:313px;height:296px;top:1275px}
.service-label{width:308px;height:88px;top:1526px;background:var(--black);color:var(--white);font-size:21px;display:flex;align-items:center;justify-content:space-between;padding:0 24px}

/* about */
.about-img{left:446px;top:1761px;width:754px;height:545px;background:linear-gradient(135deg,#9aa2aa,#c9b9a6 55%,#e6e1dc)}
.card{background:var(--white);box-shadow:0 0 20px rgba(0,0,0,.15);padding:56px 40px 0 62px}
.about-card{left:91px;top:1801px;width:582px;height:465px}
.card h3{font-size:37px;color:#111;margin-bottom:26px}
.card p{font-size:17px;line-height:32px;color:#444;margin-bottom:12px}
.btn-dark{background:var(--black);color:var(--white);font-weight:700;font-size:16px;height:47px;padding:0 24px;margin-top:12px;text-transform:uppercase}

/* blog */
.blog-img{left:0;top:2448px;width:754px;height:545px;background:linear-gradient(180deg,var(--sky) 0%,#a77d6a 45%,#3f5a3a 80%,#2f4536 100%)}
.blog-card{left:526px;top:2488px;width:581px;height:465px;padding:44px 42px 0 45px}
.blog-card h3{margin-bottom:18px}
.post-title{font-size:16px;line-height:22px;color:#222}
.post-meta{display:flex;justify-content:space-between;font-size:15px;color:#222;margin:6px 0 20px}
.blog-card p{font-size:17px;line-height:33px}

/* ebook */
.ebook{left:0;top:3138px;width:1200px;height:336px;background:var(--black);color:var(--white)}
.ebook h3{left:90px;top:62px;font-size:34px}
.ebook p{left:90px;top:120px;font-size:17px;line-height:29px;color:var(--muted)}
.btn-pdf{left:90px;top:206px;width:256px;height:54px;border:2px solid var(--white);color:var(--white);font-size:17px;text-transform:uppercase;gap:12px}
.ebook-cover{left:690px;top:3167px;width:414px;height:388px;background:linear-gradient(160deg,#5a5a5a,#1a1a1a 45%,#9b6a3d 75%,#d8d8d8);transform:skewY(-4deg)}

/* footer */
.site-footer{left:0;top:3474px;width:1200px;height:535px;background:linear-gradient(180deg,#1d3240 0%,var(--sea) 45%,#173040 100%);color:var(--white)}
.foot-col{top:184px}
.foot-col h4{font-size:22px;font-weight:500;letter-spacing:2px;margin-bottom:22px;text-transform:uppercase}
.foot-col li{list-style:none;font-size:16px;line-height:34px}
.newsletter{left:803px;top:246px;width:306px;height:50px;border-radius:25px;background:var(--white);display:flex;align-items:center;justify-content:space-between;padding-left:22px;font-size:12px;color:#777}
.newsletter span.send{height:50px;width:106px;border-radius:25px;background:var(--black);color:var(--white);font-size:17px;display:flex;align-items:center;justify-content:center}
.follow{left:803px;top:336px;font-size:22px;font-weight:500;letter-spacing:2px;text-transform:uppercase}
.socials{left:805px;top:388px;display:flex;gap:22px}
.socials span{width:14px;height:14px;border-radius:50%;background:var(--white)}
.copyright{left:0;top:486px;width:1200px;text-align:center;font-size:13px}
</style>
</head>
<body>

<header class="site-header abs">
  <div class="brand abs"><span class="brand-mark"></span>Tessly Realty</div>
  <nav class="main-nav abs">
    <span>Home</span><span>About Us</span><span>Services</span><span>Contact Us</span>
    <span>More<svg width="14" height="8" viewBox="0 0 14 8"><path d="M0 0h14L7 8z" fill="#fff"/></svg></span>
  </nav>
</header>

<div class="top-bar abs">
  <div class="left abs">
    <span><svg width="16" height="16" viewBox="0 0 24 24"><path d="M6.6 10.8a15 15 0 0 0 6.6 6.6l2.2-2.2a1 1 0 0 1 1-.25 11 11 0 0 0 3.6.6 1 1 0 0 1 1 1V20a1 1 0 0 1-1 1A17 17 0 0 1 3 4a1 1 0 0 1 1-1h3.5a1 1 0 0 1 1 1 11 11 0 0 0 .6 3.6 1 1 0 0 1-.25 1z" fill="#222"/></svg>516-555-0142</span>
    <span><svg width="18" height="14" viewBox="0 0 18 14"><rect width="18" height="14" rx="1" fill="#222"/><path d="M1 1l8 6 8-6" stroke="#fff" stroke-width="1.5" fill="none"/></svg>Email me</span>
  </div>
  <div class="right abs"><span>Have an account? Sign In</span><span>Create Account</span></div>
</div>

<section class="hero abs" role="img" aria-label="Brooklyn brownstone street with trees and stoops">
  <h1 class="hero-title display abs">Assisting landlords increase<br>profits while decreasing the stress.</h1>
  <div class="hero-dots abs"><span></span><span></span><span></span><span></span></div>
</section>

<section class="intro abs">
  <h2 class="abs">Tessly Realty NYC specializes in assisting landlords</h2>
  <p class="abs">by increasing their profits while decreasing their stress.</p>
  <span class="btn btn-outline abs">Learn More</span>
  <span class="btn btn-light abs">Contact us</span>
</section>

<h2 class="section-title display abs">How we can help</h2>
<div class="service-img abs" style="left:88px;background:linear-gradient(160deg,#e8e6e2,#b8aa98 60%,#6e5e4d)" role="img" aria-label="Bright modern apartment interior"></div>
<div class="service-img abs" style="left:444px;background:linear-gradient(160deg,#bcc7d0,#8a5a44 45%,#5a3a2c)" role="img" aria-label="Brick multifamily building with fire escapes"></div>
<div class="service-img abs" style="left:797px;background:linear-gradient(180deg,#c8d2da,#8d9a7a 50%,#5f6f4e)" role="img" aria-label="Aerial view of Florida land and lakes"></div>
<div class="service-label abs" style="left:74px">Multi-Family Leasing<svg width="12" height="12" viewBox="0 0 12 12"><path d="M1 1l5 5-5 5M6 1l5 5-5 5" stroke="#fff" stroke-width="2" fill="none"/></svg></div>
<div class="service-label abs" style="left:428px">Multi-Family Sales<svg width="12" height="12" viewBox="0 0 12 12"><path d="M1 1l5 5-5 5M6 1l5 5-5 5" stroke="#fff" stroke-width="2" fill="none"/></svg></div>
<div class="service-label abs" style="left:782px">Site Selection Advisory<svg width="12" height="12" viewBox="0 0 12 12"><path d="M1 1l5 5-5 5M6 1l5 5-5 5" stroke="#fff" stroke-width="2" fill="none"/></svg></div>

<div class="about-img abs" role="img" aria-label="Couple receiving house keys"></div>
<article class="card about-card abs">
  <h3 class="display">About us</h3>
  <p>Tessly Realty NYC-PB is a full-service real estate brokerage firm with offices located in Brooklyn, New York and West Palm Beach, Florida. Our firm focuses on multifamily leasing, sales and Commercial Real Estate Site Selection Advisory.</p>
  <p>Our clients are private and institutional multifamily real estate investors.</p>
  <span class="btn btn-dark">Learn More</span>
</article>

<div class="blog-img abs" role="img" aria-label="West Palm Beach skyline with palm trees"></div>
<article class="card blog-card abs">
  <h3 class="display">Blog</h3>
  <div class="post-title">Brooklyn, NY To West Palm Beach Florida...The Best Of Both Worlds</div>
  <div class="post-meta"><span>By | General | 1 Comment</span><span>August 3, 2018</span></div>
  <p>Tessly Realty NYC is a full service real estate brokerage firm located in Brooklyn, NY and West Palm Beach, FL. We specialize in multifamily sales and leasing, short-sales and 1031 Exchange property appropriation...</p>
  <span class="btn btn-dark">Read More</span>
</article>

<section class="ebook abs">
  <h3 class="display abs">Ebook</h3>
  <p class="abs">An ebook to be downloaded and information on my probate sales<br>and multifamily leasing marketing campaigns</p>
  <span class="btn btn-pdf abs"><svg width="16" height="20" viewBox="0 0 16 20"><path d="M1 1h9l5 5v13H1z M10 1v5h5" stroke="#fff" stroke-width="1.5" fill="none"/></svg>Download PDF</span>
</section>

<footer class="site-footer abs" role="img" aria-label="Aerial view of Florida coastline at dusk">
  <div class="foot-col abs" style="left:88px"><h4>Links</h4><ul><li>Home</li><li>About Us</li><li>Services</li><li>Contact Us</li><li>More</li></ul></div>
  <div class="foot-col abs" style="left:285px"><h4>Specialising</h4><ul><li>Residential leasing</li><li>Multifamily sales</li><li>1031 Exchange</li><li>appropriation</li></ul></div>
  <div class="foot-col abs" style="left:529px"><h4>Contact us</h4><ul><li>561-555-0187</li><li>hello@tesslyrealty.com</li><li>248 Linden Row 2</li><li>Brooklyn, New York 11237</li></ul></div>
  <div class="foot-col abs" style="left:803px"><h4>Newsletter</h4></div>
  <div class="newsletter abs"><span>Enter Your Email Address</span><span class="send">Send</span></div>
  <div class="follow abs">Follow us</div>
  <div class="socials abs"><span></span><span></span><span></span><span></span></div>
  <div class="copyright abs">Copyrights © 2019 The company Name. All Rights Reserved.</div>
</footer>

<div class="ebook-cover abs" role="img" aria-label="Ebook cover showing a kitchen interior"></div>

</body>
</html>
```